BVM Marketing Postcard

Design a 2 Sided marketing postcard for our Real estate management caompany. Looking for a professional yet fresh look that will be printed on a 6"x9" glossy flier

Contact information is www.brixleymanagement.example brixleymanagement@postwellmail.example and 555-014-7283

WE are targeting small condo and town home properties to take on their administrative responsibilities of management

```html
<!DOCTYPE html>
<html lang="en">
<head>
<meta charset="utf-8">
<title>Brixley Property Services Postcard</title>
<link href="https://fonts.googleapis.com/css2?family=Montserrat:wght@400;500;600;700;800&display=swap" rel="stylesheet">
<style>
  :root {
    --navy: #1f2c5c;
    --slate: #45557f;
    --slate-panel: #4a5a86;
    --white: #ffffff;
    --ink: #1f2c5c;
    --photo-light: #d9d9d9;
    --photo-dark: #5a5a5a;
    --page: #ffffff;
  }
  * { box-sizing: border-box; margin: 0; padding: 0; }
  html, body { width: 1200px; height: 1200px; overflow: hidden; background: var(--page); }
  body { position: relative; font-family: "Montserrat", sans-serif; color: var(--white); }

  /* Front side */
  .front { position: absolute; left: 24px; top: 23px; width: 783px; height: 527px; }
  .front-photo {
    position: absolute; left: 0; top: 0; width: 400px; height: 527px;
    background: linear-gradient(160deg, var(--photo-light) 0%, #a8a8a8 45%, var(--photo-dark) 100%);
  }
  .call-box {
    position: absolute; left: 106px; top: 227px; width: 246px; height: 116px;
    background: var(--navy); border: 4px solid var(--navy); outline: 3px solid var(--white); outline-offset: -10px;
    text-align: center; padding-top: 22px;
  }
  .call-box .call-label { font-size: 29px; font-weight: 400; letter-spacing: 1px; line-height: 1; }
  .call-box .call-number { font-size: 29px; font-weight: 700; margin-top: 6px; line-height: 1; }

  .front-panel {
    position: absolute; left: 400px; top: 0; width: 383px; height: 527px;
    background: var(--slate); text-align: center;
  }
  .tagline-small { margin-top: 34px; font-size: 14px; font-weight: 700; letter-spacing: .3px; }
  .tagline-main { margin-top: 10px; font-size: 16px; font-weight: 800; letter-spacing: .2px; }
  .tagline-sub { margin-top: 10px; font-size: 14px; font-weight: 500; }

  .brand-name { font-weight: 700; line-height: 1.15; text-align: center; }
  .front-panel .brand-name { margin-top: 34px; font-size: 27px; height: 62px; }

  .benefits {
    margin: 20px auto 0; width: 356px; border: 3px solid var(--white);
    padding: 13px 4px 12px; list-style: none;
  }
  .benefits li { font-size: 11.6px; font-weight: 500; line-height: 14px; margin-bottom: 14px; }
  .benefits li:last-child { margin-bottom: 0; }

  .pricing-line { position: absolute; left: 534px; width: 108px; height: 2px; background: var(--white); }
  .pricing-text { position: absolute; left: 472px; top: 486px; font-size: 11px; font-weight: 700; white-space: nowrap; line-height: 14px; }
  .pricing-text .small { font-size: 9px; font-weight: 400; }
  .pricing-text .amount { font-size: 15px; font-weight: 800; }

  /* Back side */
  .back { position: absolute; left: 386px; top: 617px; width: 777px; height: 524px; background: var(--white); }
  .back-header { position: absolute; left: 0; top: 0; width: 777px; height: 73px; background: var(--navy);
    display: flex; align-items: center; justify-content: center; }
  .back-header .brand-name { font-size: 24px; }

  .back-left {
    position: absolute; left: 0; top: 76px; width: 389px; height: 394px;
    background: var(--slate-panel); padding: 20px 14px 0 28px;
  }
  .back-right { position: absolute; left: 391px; top: 76px; width: 386px; height: 394px; padding: 20px 24px 0 13px; color: var(--ink); }
  .section-title {
    display: inline-block; font-size: 13.5px; font-weight: 800; letter-spacing: .3px;
    border: 2px solid var(--white); padding: 8px 7px 7px;
  }
  .back-right .section-title { border-color: var(--navy); color: var(--navy); }
  .copy { font-size: 13.2px; line-height: 15.5px; text-align: justify; hyphens: manual; }
  .back-left .copy { margin-top: 15px; }
  .back-left .section-title.second { margin-top: 14px; }
  .back-left .why .copy:first-child { margin-top: 17px; }
  .back-right .copy { margin-top: 15px; }
  .back-right .copy:first-of-type { margin-top: 26px; }

  .back-footer {
    position: absolute; left: 0; top: 470px; width: 777px; height: 54px; background: var(--navy);
    display: flex; align-items: center; justify-content: center; gap: 14px;
    font-size: 13.5px; font-weight: 500;
  }
</style>
</head>
<body>

<section class="front" aria-label="Postcard front">
  <div class="front-photo" role="img" aria-label="Black and white photograph of a modern apartment building with stacked balconies"></div>
  <div class="call-box">
    <p class="call-label">CALL</p>
    <p class="call-number">555-014-7283</p>
  </div>

  <div class="front-panel">
    <p class="tagline-small">COST EFFECTIVE</p>
    <p class="tagline-main">PROPERTY MANAGEMENT SOLUTION</p>
    <p class="tagline-sub">for 3-10 unit buildings</p>

    <p class="brand-name">BRIXLEY<br>PROPERTY SERVICES</p>

    <ul class="benefits">
      <li>Utilize our economies of scale to reduce costs across existing services&nbsp; (trash, insurance, maintenance, etc)</li>
      <li>Eliminate the unfair burden placed on a few owners to do all the work while others free-ride</li>
      <li>Improve communication amongst all owners</li>
      <li>The association’s board of directors maintain all decision making power</li>
      <li>Utilize our vetted service providers for prompt job completion and fair pricing</li>
    </ul>
  </div>
  <span class="pricing-line" style="top:479px;"></span>
  <span class="pricing-line" style="top:506px;"></span>
  <p class="pricing-text">Prices starting <span class="small">as low as</span> <span class="amount">$ 100</span>/<span class="small">month</span></p>
</section>

<section class="back" aria-label="Postcard back">
  <header class="back-header">
    <p class="brand-name">BRIXLEY PROPERTY SERVICES</p>
  </header>

  <div class="back-left">
    <h2 class="section-title">WHO WE ARE</h2>
    <p class="copy">A professional services organization with a focus on small (3-10 unit) residential buildings.</p>
    <p class="copy">Over 30 years of combined experience in real estate and property management.</p>
    <p class="copy">Professional, courteous, timely service that is tech&shy;nologically driven.</p>
    <h2 class="section-title second">WHY USE BVM?</h2>
    <div class="why">
      <p class="copy">Owners are rarely suited to manage associations and the burden often falls unfairly on one or two individuals to do all the work.</p>
      <p class="copy">Low monthly fees tailored to your needs.</p>
      <p class="copy">The Association’s board of directors maintains con&shy;trol of all decision making.</p>
    </div>
  </div>

  <div class="back-right">
    <h2 class="section-title">WHAT WE DO</h2>
    <p class="copy">Remove the administrative burden of managing small residential buildings</p>
    <p class="copy">Utilize economies of scale to reduce expense for all owners across a wide variety of services.</p>
    <p class="copy">Collect all assessments and pay all bills</p>
    <p class="copy">Provide access to BVM’s client portal with central repository of all association materials (by-laws, financials, meeting minutes, communications etc)</p>
    <p class="copy">Issue 1099’s to all contractors as required by law</p>
    <p class="copy">Prepare monthly accounting reconciliations &amp; year-end financial statements</p>
    <p class="copy">Lender and legal HOA documents for mortgage companies and sales.</p>
  </div>

  <footer class="back-footer">
    <span>www.brixleymanagement.example</span><span>|</span>
    <span>brixleymanagement@postwellmail.example</span><span>|</span>
    <span>555-014-7283</span>
  </footer>
</section>

</body>
</html>
```